Seeking a new website design for electrical contracting company

Brisket & Vane electrical contracting needs a new website for brisket-vane.example

We are looking for modern and something real cool with motion for a landing page. we have some cool images from our photo shoot. maybe even 3d motion our existing logo. we would like something we can edit with news and events and update a past project page. Also allow to take payment
stock images at
https://lorapellwinphotos.picvault-demo.example/Brisket-and-Vane

Target Market(s)

construction , home owners , business owners,

Industry/Entity Type

construction , electrical

Coding

Number of Pages Required

5+ page

Font styles to use
Serif
Sans Serif

Colors
0054AA
0677BA
7BADD7
CADEEF
E8F1F8
0094D4
00A9DD
6FCCEA
C7EBF8
E9F6FB
FFF300
FFF600
FEFA6F
FFFEC7
FFFEE8

Requirements
Must have
• excitement, motion, selling professionalism,

```html
<!DOCTYPE html>
<html lang="en">
<head>
<meta charset="utf-8">
<title>Brisket &amp; Vane Electrical Contractors</title>
<link rel="stylesheet" href="https://fonts.googleapis.com/css2?family=Josefin+Sans:wght@400;600;700&family=Lato:wght@400;700&display=swap">
<style>
:root{
  --navy:#262b6e;
  --navy-deep:#1d2160;
  --orange:#f5821f;
  --orange-soft:#fbb46b;
  --lavender:#e7eafb;
  --ink:#2a2a3a;
  --muted:#5a5d6e;
  --line:#d9dbe6;
  --white:#ffffff;
}
*{box-sizing:border-box;margin:0;padding:0}
html,body{width:1200px;height:4601px;overflow:hidden;background:var(--white)}
body{font-family:"Lato",sans-serif;color:var(--ink);position:relative}
.page{position:relative;width:1200px;height:4601px;overflow:hidden}
.abs{position:absolute}
h1,h2,h3,.heading{font-family:"Josefin Sans",sans-serif}
.btn{display:inline-block;background:var(--orange);color:var(--white);font-family:"Josefin Sans",sans-serif;font-weight:700;font-size:16px;padding:10px 14px 7px;border-radius:6px;box-shadow:0 0 0 2px rgba(255,255,255,.7)}
.bolt{display:inline-block;width:14px;height:38px;vertical-align:-4px;margin-left:6px}
.section-title{font-size:44px;font-weight:400;color:var(--ink);text-align:center;letter-spacing:.5px}
.section-title b{color:var(--navy);font-weight:700}

/* top bar */
.topbar{top:0;left:0;width:1200px;height:36px;background:var(--navy)}
.topbar .call{position:absolute;left:0;top:0;width:425px;height:36px;background:var(--orange);color:var(--white);font-family:"Josefin Sans",sans-serif;font-weight:600;font-size:15px;padding:10px 0 0 118px}
.topbar .call svg{position:absolute;left:112px;top:9px}
.topbar .mail{position:absolute;left:720px;top:10px;color:var(--white);font-size:14px}
.topbar .mail b{font-weight:700}
.topbar .sep{position:absolute;left:980px;top:8px;width:2px;height:20px;background:var(--white)}
.socials{display:flex;gap:4px}
.socials span{width:18px;height:18px;border-radius:50%;background:var(--white)}
.topbar .socials{position:absolute;left:1005px;top:9px}

/* nav */
.navbar{top:36px;left:0;width:1200px;height:68px;background:var(--white);z-index:3}
.brand{position:absolute;left:112px;top:18px;display:flex;align-items:center;gap:10px;font-family:"Josefin Sans",sans-serif;font-weight:700;font-size:26px;color:var(--navy)}
.brand i{display:block;width:42px;height:42px;background:var(--navy);border-radius:6px}
.menu{position:absolute;left:458px;top:30px;display:flex;gap:36px;font-size:16px;color:var(--ink)}
.menu .active{color:var(--orange)}
.navbar .btn{position:absolute;left:972px;top:19px;font-size:16px;padding:10px 14px 7px}

/* hero */
.hero{top:104px;left:0;width:1200px;height:660px}
.hero-photo{position:absolute;inset:0;background:linear-gradient(100deg,#1b2063 0%,#283070 38%,#5b5f7c 60%,#b7793f 78%,#8a8c98 100%);clip-path:polygon(0 0,100% 0,100% 520px,50% 660px,0 520px)}
.hero-line{position:absolute;left:0;top:0}
.hero h1{position:absolute;left:112px;top:152px;font-size:58px;font-weight:700;line-height:78px;color:var(--white);letter-spacing:2px}
.hero h1 span{color:var(--orange)}
.hero .btn{position:absolute;left:112px;top:400px;font-size:16px}

/* hexagons */
.hex{position:absolute;width:200px;height:230px}
.hex svg{position:absolute;inset:0}
.hex .hex-body{position:absolute;left:0;top:0;width:200px;height:230px;text-align:center;font-family:"Josefin Sans",sans-serif;font-size:17px;line-height:23px;color:var(--ink)}
.hex .ico{width:52px;height:52px;border-radius:50%;background:var(--orange);margin:0 auto 12px;position:relative}

/* about */
.about-photo{left:111px;top:937px;width:488px;height:425px;background:linear-gradient(180deg,#0b0b0f 0%,#202026 45%,#4d4a48 75%,#3a3835 100%)}
.about-years{left:420px;top:937px;width:180px;height:155px;background:var(--white);padding:12px 0 0 32px}
.about-years .num{font-family:"Josefin Sans",sans-serif;font-weight:700;font-size:50px;color:var(--orange)}
.about-years .lbl{font-family:"Josefin Sans",sans-serif;font-size:24px;line-height:35px;color:var(--ink)}
.about-text{left:646px;top:928px;width:450px}
.about-text h2{font-size:44px;font-weight:400}
.about-text h2 b{color:var(--navy)}
.about-text p{font-size:14px;line-height:32.5px;color:var(--muted);margin-top:6px}
.about-text p+p{margin-top:4px}
.about-text .btn{margin-top:14px;font-size:16px}

/* services */
.services{top:1447px;left:0;width:1200px;height:664px;background:var(--lavender);clip-path:polygon(90px 0,1200px 0,1200px 100%,0 100%,0 90px)}
.services .section-title{position:absolute;left:0;width:1200px;top:60px}
.svc-card{position:absolute;top:139px;width:323px;height:450px;background:var(--white);border-radius:4px;padding:8px}
.svc-card .ph{height:270px}
.svc-card h3{font-size:17px;font-weight:600;text-align:center;margin-top:22px;color:var(--ink);letter-spacing:.5px}
.svc-card p{font-size:13px;line-height:27px;text-align:center;color:var(--muted);margin-top:10px;padding:0 12px}
.svc-card.mid h3{color:var(--navy);margin-top:42px}
.svc-card.mid p{margin-top:4px}
.svc-badge{position:absolute;left:132px;top:242px;width:60px;height:60px;border-radius:50%;background:var(--white);display:flex;align-items:center;justify-content:center}
.slider-dot{position:absolute;width:22px;height:22px;border-radius:50%;background:var(--white);border:1px solid #cfd2e6}
.slider-dot.dark{background:var(--navy);border:none}
.slider-dot::after{content:"";position:absolute;left:8px;top:7px;width:6px;height:6px;border-left:2px solid #9aa;border-bottom:2px solid #9aa;transform:rotate(45deg)}
.slider-dot.next::after{left:6px;transform:rotate(-135deg)}
.slider-dot.dark::after{border-color:var(--white)}

/* testimonials */
.testi-title{top:2190px;left:0;width:1200px}
.quote{position:absolute;top:2304px;width:464px}
.quote .avatar{position:absolute;left:0;top:0;width:80px;height:80px;border-radius:50%;background:linear-gradient(160deg,#dfe2e8,#9aa0ab)}
.quote .who{position:absolute;left:104px;top:10px;font-size:17px;color:var(--ink)}
.quote .stars{position:absolute;left:104px;top:34px;color:var(--orange);font-size:20px;letter-spacing:1px}
.quote .mark{position:absolute;right:0;top:-6px;font-family:"Josefin Sans",sans-serif;font-weight:700;font-size:70px;color:var(--orange);line-height:70px}
.quote p{position:absolute;left:0;top:92px;font-size:12.5px;line-height:26px;color:var(--muted)}
.testi-divider{left:595px;top:2292px;height:178px;border-left:3px dashed #c8c8cf}

/* projects */
.projects{top:2554px;left:0;width:1200px;height:839px;background:var(--lavender);clip-path:polygon(90px 0,1200px 0,1200px 100%,0 100%,0 90px)}
.projects .section-title{position:absolute;left:0;width:1200px;top:42px}
.proj-frame{position:absolute;left:36px;top:111px;width:1134px;height:634px;background:var(--white);padding:14px 14px;display:grid;grid-template-columns:repeat(3,1fr);grid-template-rows:repeat(2,1fr);gap:14px 16px}
.proj-frame .cell{position:relative}
.proj-feature{background:var(--navy);display:flex;flex-direction:column;align-items:center;justify-content:center}
.proj-feature::before{content:"";position:absolute;inset:10px;border:2px solid rgba(255,255,255,.85)}
.proj-feature .cat{font-family:"Josefin Sans",sans-serif;font-size:16px;color:var(--orange);letter-spacing:.5px}
.proj-feature .ttl{font-family:"Josefin Sans",sans-serif;font-weight:600;font-size:25px;color:var(--white);margin-top:14px;letter-spacing:.5px}
.proj-feature .rule{width:80px;height:4px;background:var(--orange);margin-top:12px}
.projects .btn{position:absolute;left:523px;top:781px;font-size:16px}

/* blog */
.blog-head{top:3470px;left:111px}
.blog-head h2{font-size:44px;font-weight:400}
.blog-head h2 b{color:var(--navy)}
.blog-intro{left:598px;top:3478px;width:500px;font-size:12.5px;line-height:26px;color:var(--muted)}
.post{position:absolute;top:3584px;width:314px;height:376px;background:var(--white);box-shadow:0 4px 18px rgba(30,35,90,.12);padding:0}
.post .ph{height:210px}
.post .cat{font-family:"Josefin Sans",sans-serif;font-weight:700;font-size:15px;color:var(--orange);margin:28px 0 0 14px}
.post h3{font-family:"Lato",sans-serif;font-weight:400;font-size:16px;line-height:26px;color:var(--ink);margin:8px 14px 0}
.post .meta{position:absolute;left:16px;top:332px;display:flex;gap:44px;font-size:12.5px;color:var(--muted)}
.post .meta span{display:flex;align-items:center;gap:6px}
.post .meta i{display:inline-block;width:18px;height:13px;border:1.5px solid #8a8c99;border-radius:2px}

/* footer */
.footer{top:4040px;left:0;width:1200px;height:561px}
.footer svg.cap{position:absolute;left:0;top:0}
.footer .body{position:absolute;left:0;top:0;width:1200px;height:561px;background:linear-gradient(180deg,var(--navy-deep),#242a72);clip-path:polygon(0 170px,600px 20px,1200px 170px,1200px 561px,0 561px)}
.footer .brand-foot{position:absolute;left:365px;top:160px;display:flex;align-items:center;gap:16px;font-family:"Josefin Sans",sans-serif;font-weight:700;font-size:44px;color:var(--white)}
.footer .brand-foot i{display:block;width:96px;height:96px;border-radius:50%;background:var(--white)}
.fcol{position:absolute;top:258px;color:var(--white)}
.fcol h4{font-family:"Lato",sans-serif;font-weight:700;font-size:21px;margin-bottom:14px}
.fcol li{list-style:none;font-size:16px;line-height:31.5px}
.fcol .row{display:flex;gap:14px;font-size:16px;line-height:24px;margin-bottom:17px}
.fcol .row svg{flex:none;margin-top:4px}
.news-input{width:270px;height:40px;background:var(--white);border-radius:6px;font-size:12.5px;color:var(--muted);padding:13px 16px;margin-top:6px}
.fcol .btn{margin-top:14px;font-size:16px}
.footer .socials{margin-top:30px;gap:6px}
.footer .socials span{width:30px;height:30px;background:var(--white)}
.footer .socials span:first-child{background:var(--orange)}
.foot-rule{position:absolute;left:111px;top:528px;width:978px;height:1px;background:rgba(255,255,255,.45)}
.copy{position:absolute;left:0;top:537px;width:1200px;text-align:center;font-size:13px;color:var(--white)}
</style>
</head>
<body>
<div class="page">

  <!-- top bar -->
  <div class="abs topbar">
    <div class="call">
      <svg width="18" height="18" viewBox="0 0 24 24"><path fill="#fff" d="M6.6 10.8a15.1 15.1 0 0 0 6.6 6.6l2.2-2.2c.3-.3.7-.4 1-.2 1.1.4 2.3.6 3.6.6.6 0 1 .4 1 1V20c0 .6-.4 1-1 1A17 17 0 0 1 3 4c0-.6.4-1 1-1h3.5c.6 0 1 .4 1 1 0 1.3.2 2.5.6 3.6.1.3 0 .7-.2 1z"/></svg>
      &nbsp;&nbsp;Client Services&nbsp; 1-555-014-2290
    </div>
    <div class="mail">
      <svg width="18" height="13" viewBox="0 0 18 13" style="vertical-align:-1px;margin-right:6px"><rect x="0.5" y="0.5" width="17" height="12" fill="#fff"/><path d="M1 1l8 6 8-6" stroke="#262b6e" fill="none" stroke-width="1.4"/></svg><b>Email:</b> info@brisket-vane.example
    </div>
    <div class="sep"></div>
    <div class="socials"><span></span><span></span><span></span><span></span><span></span></div>
  </div>

  <!-- nav -->
  <div class="abs navbar">
    <div class="brand"><i></i>BRISKET &amp; VANE</div>
    <div class="menu">
      <span class="active">Home</span><span>About</span><span>Services</span><span>Projects</span><span>Our Team</span><span>Blog</span>
    </div>
    <span class="btn">Contact Us</span>
  </div>

  <!-- hero -->
  <section class="abs hero">
    <svg class="hero-line" width="1200" height="680" viewBox="0 0 1200 680">
      <polygon points="0,528 600,672 1200,528 1200,540 600,684 0,540" fill="#262b6e"/>
    </svg>
    <div class="hero-photo" role="img" aria-label="Electrician in hard hat and safety glasses working on an electrical panel"></div>
    <h1>LIGHTING THE<br>FUTURE OF <span>ELECTRICAL</span><br><span>CONTRACTING.</span></h1>
    <span class="btn">Get Started</span>
  </section>

  <!-- feature hexagons -->
  <div class="hex" style="left:266px;top:598px">
    <svg viewBox="0 0 200 230" width="200" height="230"><polygon points="100,4 196,58 196,172 100,226 4,172 4,58" fill="#fff" stroke="#f5821f" stroke-width="4"/></svg>
    <div class="hex-body" style="padding-top:52px">
      <div class="ico"><svg width="52" height="52" viewBox="0 0 52 52"><circle cx="26" cy="26" r="14" fill="none" stroke="#fff" stroke-width="2.5"/><path d="M26 18v8l6 4" stroke="#fff" stroke-width="2.5" fill="none"/></svg></div>
      Ontime at Services
    </div>
  </div>
  <div class="hex" style="left:489px;top:654px">
    <svg viewBox="0 0 200 230" width="200" height="230"><polygon points="100,4 196,58 196,172 100,226 4,172 4,58" fill="#262b6e" stroke="#f5821f" stroke-width="6"/></svg>
    <div class="hex-body" style="padding-top:48px;color:#f5821f;font-weight:700">
      <div class="ico" style="background:#fff"><svg width="52" height="52" viewBox="0 0 52 52"><circle cx="26" cy="26" r="15" fill="none" stroke="#262b6e" stroke-width="3"/><text x="26" y="30" text-anchor="middle" font-family="Josefin Sans, sans-serif" font-weight="700" font-size="11" fill="#262b6e">24</text></svg></div>
      24/7 Services
    </div>
  </div>
  <div class="hex" style="left:720px;top:592px">
    <svg viewBox="0 0 200 230" width="200" height="230"><polygon points="100,4 196,58 196,172 100,226 4,172 4,58" fill="#fff" stroke="#f5821f" stroke-width="4"/></svg>
    <div class="hex-body" style="padding-top:46px">
      <div class="ico"><svg width="52" height="52" viewBox="0 0 52 52"><circle cx="26" cy="22" r="9" fill="none" stroke="#fff" stroke-width="2.5"/><path d="M20 29l-3 11 9-4 9 4-3-11" fill="none" stroke="#fff" stroke-width="2.5"/></svg></div>
      Verified<br>Professionals
    </div>
  </div>

  <!-- about -->
  <div class="abs about-photo" role="img" aria-label="Team of five electricians in dark uniforms posing together"></div>
  <div class="abs about-years">
    <div class="num">10+</div>
    <div class="lbl">Years<br>Experience</div>
  </div>
  <div class="abs about-text">
    <h2>About <b>Us</b><svg class="bolt" viewBox="0 0 14 38"><polygon points="9,0 2,20 7,20 4,38 13,15 8,15 12,0" fill="#f5821f"/></svg></h2>
    <p>We're more than just electricians — we're problem solvers, system designers, and project partners. Whether it's powering a new commercial high-rise or upgrading critical infrastructure, we bring deep expertise, attention to detail, and a relentless drive for quality.</p>
    <p>Our success is built on relationships. With our clients. With our crews. And with the communities we help grow — one circuit at a time.</p>
    <span class="btn">Read More</span>
  </div>

  <!-- services -->
  <section class="abs services">
    <h2 class="section-title">What <b>We Do</b><svg class="bolt" viewBox="0 0 14 38"><polygon points="9,0 2,20 7,20 4,38 13,15 8,15 12,0" fill="#f5821f"/></svg></h2>
    <div class="svc-card" style="left:102px">
      <div class="ph" role="img" aria-label="Electrician inspecting equipment in an industrial facility" style="background:linear-gradient(160deg,#7d8594,#4a5262 55%,#c47a3a)"></div>
      <h3>Commercial Electrical Contracting</h3>
      <p>End-to-end electrical systems for offices, retail, mixed-use, and high-rise buildings. Efficient, code-compliant, and built to scale.</p>
    </div>
    <div class="svc-card mid" style="left:438px">
      <div class="ph" role="img" aria-label="Electricians giving a thumbs up in a workshop" style="background:linear-gradient(160deg,#3c3a36,#6d5a44 55%,#2d3440)"></div>
      <div class="svc-badge"><svg width="40" height="40" viewBox="0 0 40 40"><rect x="8" y="16" width="24" height="18" fill="none" stroke="#f5821f" stroke-width="2.5"/><rect x="13" y="8" width="6" height="8" fill="#f5821f"/><rect x="22" y="11" width="6" height="5" fill="#f5821f"/></svg></div>
      <h3>Industrial Electrical Services</h3>
      <p>Heavy-duty power systems, automation wiring, and equipment installs for factories, warehouses, and energy facilities.</p>
    </div>
    <div class="svc-card" style="left:773px">
      <div class="ph" role="img" aria-label="Tool belt filled with electrician's hand tools" style="background:linear-gradient(160deg,#2a2c33,#514a40 55%,#8a6b3e)"></div>
      <h3>Service &amp; Maintenance Contracts</h3>
      <p>Preventive maintenance, emergency repairs, and system checks to keep your infrastructure running.</p>
    </div>
    <span class="slider-dot" style="left:29px;top:352px"></span>
    <span class="slider-dot next" style="left:1136px;top:352px;opacity:.5"></span>
  </section>

  <!-- testimonials -->
  <h2 class="abs section-title testi-title">Client <b>Testimonials</b><svg class="bolt" viewBox="0 0 14 38"><polygon points="9,0 2,20 7,20 4,38 13,15 8,15 12,0" fill="#f5821f"/></svg></h2>
  <div class="quote" style="left:107px">
    <div class="avatar" role="img" aria-label="Client portrait"></div>
    <div class="who">~Dana R., Project Manager,</div>
    <div class="stars">★★★★★</div>
    <div class="mark">”</div>
    <p>“Brisket &amp; Vane delivered our project ahead of schedule and under budget.<br>Their crew was professional, safe, and a pleasure to work with.”</p>
  </div>
  <div class="abs testi-divider"></div>
  <div class="quote" style="left:634px">
    <div class="avatar" role="img" aria-label="Client portrait" style="background:linear-gradient(160deg,#b9a58e,#5d6a4a)"></div>
    <div class="who">~Owen T., Facilities Director</div>
    <div class="stars">★★★★★</div>
    <div class="mark">”</div>
    <p>Top-tier work. From design to final inspection, everything was handled with<br>precision. Wouldn't trust anyone else with our electrical systems.”</p>
  </div>
  <span class="slider-dot dark" style="left:43px;top:2376px"></span>
  <span class="slider-dot next" style="left:1121px;top:2376px;background:#9a9ca8;border:none"></span>

  <!-- projects -->
  <section class="abs projects">
    <h2 class="section-title">Latest <b>Projetcs</b><svg class="bolt" viewBox="0 0 14 38"><polygon points="9,0 2,20 7,20 4,38 13,15 8,15 12,0" fill="#f5821f"/></svg></h2>
    <div class="proj-frame">
      <div class="cell" role="img" aria-label="Electrician installing a ceiling fixture" style="background:linear-gradient(160deg,#d9d9d6,#8d8b87 60%,#3a3a3c)"></div>
      <div class="cell proj-feature">
        <div class="cat">Service &amp; Maintenance Contracts</div>
        <div class="ttl">Industrial Maintenance</div>
        <div class="rule"></div>
      </div>
      <div class="cell" role="img" aria-label="Technicians in high-visibility gear at a wind turbine site" style="background:linear-gradient(160deg,#a9bfd6,#7c8c5a 55%,#44484c)"></div>
      <div class="cell" role="img" aria-label="Electrician wiring a wall-mounted panel with conduit" style="background:linear-gradient(160deg,#d6d2c9,#8d8a84 55%,#2f3038)"></div>
      <div class="cell" role="img" aria-label="Hands using pliers on a wall outlet" style="background:linear-gradient(160deg,#e7e5e1,#a9a39b 50%,#c33a2f)"></div>
      <div class="cell" role="img" aria-label="Engineer in hard hat working in a server and control room" style="background:linear-gradient(160deg,#8c93a0,#59606b 55%,#c77a3b)"></div>
    </div>
    <span class="btn">View All Projects</span>
  </section>

  <!-- blog -->
  <div class="abs blog-head">
    <h2>Latest <b>News &amp; Blog</b><svg class="bolt" viewBox="0 0 14 38"><polygon points="9,0 2,20 7,20 4,38 13,15 8,15 12,0" fill="#f5821f"/></svg></h2>
  </div>
  <p class="abs blog-intro">Lorem ipsum dolor sit amet, consectetur adipiscing elit, sed do eiusmod tempor incididunt ut labore et dolore magna aliqua. Ut enim ad minim veniam, quis nostrud exercitation ullamco laboris nisi ut aliquip ex ea commodo consequat.</p>
  <span class="slider-dot dark" style="left:47px;top:3710px"></span>
  <span class="slider-dot next" style="left:1127px;top:3710px"></span>
  <article class="post" style="left:115px">
    <div class="ph" role="img" aria-label="Electrician testing a panel with a multimeter" style="background:linear-gradient(160deg,#5e6a86,#2c3550 55%,#c46b2b)"></div>
    <div class="cat">Maintenance</div>
    <h3>Upgrading Legacy Systems: How We Modernized a 1960s Industrial Plant</h3>
    <div class="meta"><span><i></i>Apr 21,2025</span><span><i></i>4 Comments</span></div>
  </article>
  <article class="post" style="left:444px">
    <div class="ph" role="img" aria-label="Two technicians reviewing a clipboard beside control cabinets" style="background:linear-gradient(160deg,#8f949c,#4c5260 55%,#2a3350)"></div>
    <div class="cat">Tool BOx Checking</div>
    <h3>Toolbox Talk: New OSHA Safety Guidelines for 2025</h3>
    <div class="meta"><span><i></i>Apr 18,2025</span><span><i></i>4 Comments</span></div>
  </article>
  <article class="post" style="left:773px">
    <div class="ph" role="img" aria-label="Crew reviewing plans at an outdoor job site" style="background:linear-gradient(160deg,#a4683f,#7d7b78 55%,#48474a)"></div>
    <div class="cat">Service</div>
    <h3>The Future of Commercial Electrical: Smart Panels &amp; Load Management</h3>
    <div class="meta"><span><i></i>Apr 17,2025</span><span><i></i>4 Comments</span></div>
  </article>

  <!-- footer -->
  <footer class="abs footer">
    <svg class="cap" width="1200" height="180" viewBox="0 0 1200 180"><polygon points="0,150 600,0 1200,150 1200,170 600,20 0,170" fill="#f5821f"/></svg>
    <div class="body"></div>
    <div class="brand-foot"><i></i>BRISKET &amp; VANE</div>
    <div class="fcol" style="left:113px">
      <h4>Quick Links</h4>
      <ul><li>Home</li><li>About</li><li>Services</li><li>Projects</li><li>Our Team</li><li>Blog</li><li>Contact Us</li></ul>
    </div>
    <div class="fcol" style="left:311px">
      <h4>Help Links</h4>
      <ul><li>Privacy Policy</li><li>Terms &amp; Conditions</li><li>Disclaimer</li><li>FAQ's</li><li>Support</li><li>Help</li></ul>
    </div>
    <div class="fcol" style="left:530px">
      <h4>Contact Info</h4>
      <div class="row"><svg width="16" height="16" viewBox="0 0 24 24"><path fill="#fff" d="M6.6 10.8a15.1 15.1 0 0 0 6.6 6.6l2.2-2.2c.3-.3.7-.4 1-.2 1.1.4 2.3.6 3.6.6.6 0 1 .4 1 1V20c0 .6-.4 1-1 1A17 17 0 0 1 3 4c0-.6.4-1 1-1h3.5c.6 0 1 .4 1 1 0 1.3.2 2.5.6 3.6.1.3 0 .7-.2 1z"/></svg>1-555-014-2290</div>
      <div class="row"><svg width="16" height="12" viewBox="0 0 18 13"><rect x="0.5" y="0.5" width="17" height="12" fill="#fff"/><path d="M1 1l8 6 8-6" stroke="#262b6e" fill="none" stroke-width="1.4"/></svg>info@brisket-vane.example</div>
      <div class="row"><svg width="14" height="18" viewBox="0 0 14 20"><path fill="#fff" d="M7 0a7 7 0 0 0-7 7c0 5 7 13 7 13s7-8 7-13a7 7 0 0 0-7-7zm0 10a3 3 0 1 1 0-6 3 3 0 0 1 0 6z"/></svg>48 Alderbrook Dr. Millbrook<br>NH 03999</div>
    </div>
    <div class="fcol" style="left:823px;top:250px">
      <h4>Newsletter Sign Up</h4>
      <div class="news-input">Enter Email Address</div>
      <span class="btn">Subscribe</span>
      <div class="socials"><span></span><span></span><span></span><span></span><span></span></div>
    </div>
    <div class="foot-rule"></div>
    <div class="copy">© 2025 Brisket &amp; Vane Electrical Contractors. All rights reserved.</div>
  </footer>

</div>
</body>
</html>
```